Business Card Design For A Renovation Contractor Company

We need a business card for a new company based in Singapore, our company name is "RB Tolvane". We are a renovation contractor that builds designs into reality. We build more of F&B restaurants, retail stores and commercial offices. We work very closely with designers. The final design should communicate to our client that we are a company that you can trust, that will plan and complete your project without giving you a headache. I like my client to remember my company as "RB". The beauty of SIMPLE is important.

Industry/Entity Type

Contractor

Requirements
Nice to have
• Black or Red base

```html
<!DOCTYPE html>
<html lang="en">
<head>
<meta charset="utf-8">
<title>RB Tolvane – Business Card</title>
<link rel="stylesheet" href="https://fonts.googleapis.com/css2?family=Open+Sans:wght@400;600;700&family=Questrial&display=swap">
<style>
  :root {
    --ink: #0b0b0b;
    --paper: #ffffff;
    --accent: #e0202a;
    --stage: #e9e9ee;
    --rule: #555555;
    --tagline: #333333;
  }
  * { margin: 0; padding: 0; box-sizing: border-box; }
  html, body { width: 1200px; height: 987px; overflow: hidden; background: var(--stage); }
  .canvas { position: relative; width: 1200px; height: 987px; }
  .card {
    position: absolute; left: 280px; width: 640px; height: 366px;
    border-radius: 34px; overflow: hidden;
    box-shadow: 0 6px 18px rgba(0,0,0,0.18);
  }
  .card-front { top: 92px; background: var(--paper); }
  .card-back { top: 518px; background: var(--ink); }

  .front-shape { position: absolute; inset: 0; }

  .brand { position: absolute; left: 140px; top: 48px; width: 380px; text-align: center; }
  .brand-name {
    font-family: "Questrial", sans-serif; font-size: 56px; line-height: 1;
    color: var(--ink); letter-spacing: 1px; display: inline-flex; align-items: center; gap: 14px;
  }
  .brand-dot { width: 22px; height: 22px; border-radius: 50%; background: var(--accent); display: inline-block; }
  .brand-tagline {
    font-family: "Questrial", sans-serif; font-size: 20px; color: var(--tagline);
    border-bottom: 1.5px solid var(--rule); padding-bottom: 3px; margin-top: 6px; display: inline-block;
  }

  .holder {
    position: absolute; right: 48px; top: 168px;
    font-family: "Open Sans", sans-serif; font-size: 20px; color: var(--ink);
  }
  .holder-name { font-weight: 700; }
  .holder-title { color: var(--accent); font-weight: 400; }

  .contact {
    position: absolute; left: 34px; top: 238px;
    font-family: "Open Sans", sans-serif; font-size: 16px; color: var(--paper);
    display: flex; flex-direction: column; gap: 6px;
  }
  .contact-row { display: flex; align-items: center; gap: 14px; white-space: nowrap; }
  .contact-item { display: inline-flex; align-items: center; gap: 6px; }
  .icon { width: 14px; height: 14px; fill: none; stroke: var(--paper); stroke-width: 1.6; }

  .back-brand {
    position: absolute; left: 0; right: 0; top: 120px; text-align: center;
    font-family: "Questrial", sans-serif; font-size: 64px; color: var(--paper);
    display: flex; justify-content: center; align-items: center; gap: 18px;
  }
  .back-ring { width: 28px; height: 28px; border: 3px solid var(--paper); border-radius: 50%; }
  .back-web {
    position: absolute; left: 0; right: 0; top: 232px; text-align: center;
    font-family: "Open Sans", sans-serif; font-size: 18px; letter-spacing: 5px; color: var(--paper);
  }
</style>
</head>
<body>
<main class="canvas">
  <section class="card card-front">
    <svg class="front-shape" width="640" height="366" viewBox="0 0 640 366">
      <path d="M0,150 Q330,175 640,366 L0,366 Z" fill="var(--ink)"/>
      <path d="M0,138 Q340,162 640,352" fill="none" stroke="var(--accent)" stroke-width="3"/>
    </svg>

    <div class="brand">
      <div class="brand-name"><span class="brand-dot"></span>RB Tolvane</div>
      <div class="brand-tagline">planned well, built to last</div>
    </div>

    <p class="holder"><span class="holder-name">Your Name,</span> <span class="holder-title">Title</span></p>

    <div class="contact">
      <div class="contact-row">
        <span class="contact-item">
          <svg class="icon" viewBox="0 0 16 16"><path d="M3 2 L6 2 L7 5 L5 6.5 Q6.5 9.5 9.5 11 L11 9 L14 10 L14 13 Q8 14 2.5 8 Q2 5 3 2 Z"/></svg>
          123-456-0789
        </span>
        <span class="contact-item">
          <svg class="icon" viewBox="0 0 16 16"><rect x="4" y="1.5" width="8" height="13" rx="1.5"/><line x1="7" y1="12" x2="9" y2="12"/></svg>
          123-456-0789
        </span>
      </div>
      <div class="contact-row">
        <span class="contact-item">
          <svg class="icon" viewBox="0 0 16 16"><rect x="1.5" y="3.5" width="13" height="9"/><path d="M1.5 3.5 L8 9 L14.5 3.5"/></svg>
          info@rbtolvane.com
        </span>
        <span class="contact-item">
          <svg class="icon" viewBox="0 0 16 16"><circle cx="8" cy="8" r="6.5"/><ellipse cx="8" cy="8" rx="3" ry="6.5"/><line x1="1.5" y1="8" x2="14.5" y2="8"/></svg>
          www.rbtolvane.com
        </span>
      </div>
      <div class="contact-row">Street Name, City Name, State Zip Code</div>
    </div>
  </section>

  <section class="card card-back">
    <div class="back-brand"><span class="back-ring"></span>RB Tolvane</div>
    <p class="back-web">www.rbtolvane.com</p>
  </section>
</main>
</body>
</html>
```